Business Card Design Project

We are a construction company in Orange County, CA. We need a two sided business card. We would like the back to be our logo with web URL. Front should included Name, title, address, phone, fax and email address.

our address is
627 West Dorrance Blvd, Suite 308
Anaheim, CA 92718

Our logo files are attached.

Construction

```html
<!DOCTYPE html>
<html lang="en">
<head>
<meta charset="utf-8">
<title>VELDRO Business Card</title>
<link href="https://fonts.googleapis.com/css2?family=Source+Sans+3:wght@400;700;900&display=swap" rel="stylesheet">
<style>
  :root {
    --backdrop: #9a6a44;
    --card-white: #ffffff;
    --brand-blue: #1a4a80;
    --ink-grey: #555555;
    --rule-grey: #b5b5b5;
    --band-grey: #6f6f6f;
    --back-light: #6b6b6b;
    --back-dark: #3c3c3c;
  }
  * { margin: 0; padding: 0; box-sizing: border-box; }
  html, body { width: 1200px; height: 402px; overflow: hidden; }
  body {
    background: var(--backdrop);
    font-family: "Source Sans 3", "Myriad Pro", sans-serif;
    position: relative;
  }
  .card {
    position: absolute;
    top: 71px;
    width: 512px;
    height: 292px;
    box-shadow: 0 2px 8px rgba(0,0,0,.35);
    overflow: hidden;
  }
  .card--front { left: 71px; background: var(--card-white); }
  .card--back {
    left: 639px;
    background: linear-gradient(110deg, var(--back-light), var(--back-dark));
  }
  .holder {
    position: absolute; top: 22px; width: 100%;
    text-align: center; font-size: 15px; color: var(--ink-grey);
  }
  .holder strong { color: var(--brand-blue); font-weight: 700; }
  .wordmark {
    position: absolute; width: 100%; text-align: center;
    font-weight: 900; letter-spacing: -1px; line-height: 1;
  }
  .card--front .wordmark { top: 72px; font-size: 86px; color: var(--brand-blue); }
  .card--back .wordmark { top: 106px; font-size: 86px; color: var(--card-white); }
  .rule {
    position: absolute; left: 50px; top: 205px; width: 412px; height: 2px;
    background: linear-gradient(90deg, transparent, var(--rule-grey) 15%, var(--ink-grey) 50%, var(--rule-grey) 85%, transparent);
  }
  .contacts {
    position: absolute; top: 226px; left: 40px;
    display: flex; font-size: 13px; color: var(--ink-grey); line-height: 18px;
  }
  .contacts .col { padding: 0 10px; border-left: 1px solid var(--ink-grey); }
  .contacts .col:first-child { border-left: none; padding-left: 0; }
  .contacts .line { display: flex; align-items: center; gap: 5px; white-space: nowrap; }
  .contacts svg { width: 10px; height: 10px; fill: var(--brand-blue); flex: none; }
  .footer-band { position: absolute; left: 0; bottom: 0; width: 512px; height: 14px; }
</style>
</head>
<body>
  <section class="card card--front">
    <p class="holder"><strong>Your Name,</strong> Title</p>
    <p class="wordmark">VELDRO</p>
    <div class="rule"></div>
    <div class="contacts">
      <div class="col">
        <div class="line">
          <svg viewBox="0 0 10 10"><path d="M2 0.5 L3.8 2.6 3 3.8 Q4.2 6 6.2 7 L7.4 6.2 9.5 8 8.4 9.6 Q3 9 0.4 1.6 Z"/></svg>01-234-5678</div>
        <div class="line">
          <svg viewBox="0 0 10 10"><rect x="2" y="0.5" width="6" height="3"/><rect x="0.5" y="4" width="9" height="4.5" rx="1"/><rect x="2.5" y="8" width="5" height="1.5"/></svg>01-234-5678</div>
      </div>
      <div class="col">
        <div class="line">
          <svg viewBox="0 0 10 10"><rect x="0.5" y="2" width="9" height="6.5"/><path d="M0.5 2 L5 5.5 9.5 2" fill="none" stroke="#fff" stroke-width="1"/></svg>info@veldrobuild.com</div>
        <div class="line">
          <svg viewBox="0 0 10 10"><circle cx="5" cy="5" r="4.6"/><path d="M0.5 5 H9.5 M5 0.5 V9.5" stroke="#fff" stroke-width="0.8"/></svg>www.veldrobuild.com</div>
      </div>
      <div class="col">
        <div class="line">627 West Dorrance Blvd, Suite 308</div>
        <div class="line">Anaheim, CA 92718</div>
      </div>
    </div>
    <svg class="footer-band" viewBox="0 0 512 14" preserveAspectRatio="none">
      <polygon points="0,4 262,4 248,14 0,14" fill="#1a4a80"/>
      <polygon points="278,0 512,0 512,14 264,14" fill="#6f6f6f"/>
    </svg>
  </section>

  <section class="card card--back">
    <p class="wordmark">VELDRO</p>
  </section>
</body>
</html>
```